VitaBraid Web Design. Health and Wellness Industry

We are in process of creating next big Cloud based Health Care Management system. We have created 1st draft of Landing Page design. It is missing curb appeal, jazzy feel and engaging modern look.

Need a talented designer to recreate UI/ UX and take it to the next level.
If you are a creative designer, gifted with vision and imagination, I strongly encourage you to participate.

I want the designers to stay focus on the Landing page
Once we select the winner we will provide other subsequent pages
Follow up pages will be similar simple design

Target Market(s)

Individual Users and small business
Age Group 35-75
Individuals involved in "Health and Fitness" activity tracking, managing etc.

Industry/Entity Type

Health And Wellness

Number of Pages Required

5+ page

Colors
f68e4e
34a6d7

Requirements
Must have
• Super Engaging UI/ UX
• Smart and Contemporary look
• Easy to Navigate
• Folder Style menu bar
• Slideshow
• Social Medial Friendly
• Online Shopping
Nice to have
• Start from the enclosed draft Landing Page Idea.
• Feel Free to include additional frame, information section, Icon etc.

```html
<!DOCTYPE html>
<html lang="en">
<head>
<meta charset="utf-8">
<title>VitaBraid – Cloud Based Health Care Management</title>
<link rel="stylesheet" href="https://fonts.googleapis.com/css2?family=Open+Sans:ital,wght@0,400;0,600;0,700;1,400&family=Ubuntu:wght@400;500&display=swap">
<style>
:root{
  --blue:#34a6d7;
  --blue-dark:#2a8fbb;
  --orange:#f68e4e;
  --orange-dark:#e2783a;
  --green:#8dc63f;
  --green-dark:#76ad2c;
  --ink:#4a4a4a;
  --muted:#8a8a8a;
  --light:#f3f4f5;
  --line:#e3e5e7;
  --white:#ffffff;
}
*{box-sizing:border-box;margin:0;padding:0}
html,body{width:1200px;height:3964px;overflow:hidden}
body{font-family:"Open Sans",Arial,sans-serif;color:var(--ink);background:var(--white);font-size:13px;line-height:1.55}
.container{width:960px;margin:0 auto;position:relative}
.btn{display:inline-block;background:var(--orange);color:var(--white);font-size:11px;font-weight:700;text-transform:uppercase;padding:6px 16px;border-radius:2px;letter-spacing:.5px}
.section-title{font-family:"Ubuntu",sans-serif;font-weight:500;text-transform:uppercase;font-size:20px;text-align:center;letter-spacing:.5px}

/* top bar */
.topbar{height:40px;background:var(--blue)}
.topbar .container{height:40px;display:flex;align-items:center;justify-content:space-between}
.search{width:180px;height:24px;background:var(--white);border-radius:12px;display:flex;align-items:center;padding:0 10px;color:var(--muted);font-size:11px;gap:6px}
.top-links{display:flex;align-items:center;gap:14px;color:var(--white);font-size:11px}
.top-links .btn{padding:4px 12px;font-size:10px}

/* header */
.header{height:112px;background:var(--white);border-bottom:1px solid var(--line)}
.header .container{height:112px;display:flex;align-items:center;justify-content:space-between}
.logo{display:flex;align-items:center;gap:10px}
.logo-dot{width:30px;height:30px;border-radius:50%;background:var(--orange)}
.logo-name{font-size:34px;font-weight:600;color:var(--orange);line-height:1}
.logo-tag{font-size:10px;color:var(--muted);margin-top:4px}
.nav{display:flex;height:112px}
.nav-item{width:96px;display:flex;flex-direction:column;align-items:center;justify-content:center;gap:8px;font-size:12px;color:var(--ink);border-left:1px solid var(--line)}
.nav-item:last-child{border-right:1px solid var(--line)}
.nav-item.active{background:var(--light)}

/* hero */
.hero{height:468px;background:linear-gradient(180deg,#f7f8f9,#e9ecef);position:relative;overflow:hidden}
.hero-copy{position:absolute;left:170px;top:140px}
.hero-copy .kicker{font-size:24px;color:var(--orange);font-weight:600}
.hero-copy h1{font-family:"Ubuntu",sans-serif;font-weight:400;font-size:40px;color:#5a5f63;line-height:1.15;margin:4px 0 20px}
.hero-photo{position:absolute;right:0;top:0;width:520px;height:468px;background:linear-gradient(120deg,#eef2f5 10%,#b9d6e8 55%,#2f5f86)}
.dots{position:absolute;left:170px;top:430px;display:flex;gap:8px}
.dots span{width:10px;height:10px;border-radius:50%;background:#c9ced2}
.dots span:first-child{background:var(--blue)}

/* features */
.features{height:428px;background:var(--light);padding-top:60px;border-top:1px solid var(--line)}
.feature-row{display:flex;gap:20px}
.feature{width:225px;height:300px;background:var(--green);border:4px solid var(--white);box-shadow:0 2px 6px rgba(0,0,0,.12);color:var(--white);text-align:center;padding:22px 18px}
.feature h3{font-family:"Ubuntu",sans-serif;font-weight:400;font-size:24px;margin:10px 0 10px;line-height:1}
.feature p{font-size:11px;line-height:1.6;margin-bottom:16px;color:#f4fbe9}

/* success story */
.story{height:392px;background:var(--blue);color:var(--white);padding-top:48px}
.title-lines{display:flex;align-items:center;justify-content:center;gap:18px}
.title-lines::before,.title-lines::after{content:"";width:90px;height:1px;background:rgba(255,255,255,.6)}
.story-body{display:flex;gap:36px;margin:56px 0 0 80px;width:800px}
.avatar{width:120px;height:130px;background:var(--white);padding:6px;flex:none}
.avatar div{width:100%;height:100%;background:linear-gradient(160deg,#d9e6ee,#8fb3c9)}
.story-text p{font-size:12px;line-height:1.75;color:#eaf6fc}
.story-name{font-size:17px;font-weight:700;font-style:italic;margin-top:14px}
.story-role{font-size:11px;color:#d5ecf7}
.arrow{position:absolute;top:150px;font-size:28px;color:var(--white)}

/* videos */
.videos{height:680px;background:var(--orange);padding-top:48px;color:var(--white)}
.video-frame{margin:40px auto 0;width:940px;height:472px;border:6px solid rgba(255,255,255,.85);border-radius:6px;background:linear-gradient(110deg,#dbe8f0 0%,#9fc5dd 45%,#3b7ea9);position:relative;box-shadow:0 10px 24px rgba(0,0,0,.18)}
.play{position:absolute;left:50%;top:50%;transform:translate(-50%,-50%)}

/* products */
.products{height:980px;background:#f7f7f7;padding-top:48px}
.products .section-title{color:var(--blue)}
.product-grid{display:grid;grid-template-columns:repeat(3,300px);gap:24px 30px;margin-top:48px}
.product{height:376px;background:var(--white);border:1px solid var(--line);text-align:center;padding:18px}
.product-img{height:200px;background:linear-gradient(160deg,#fafafa,#e2e4e6)}
.product h4{font-family:"Ubuntu",sans-serif;font-weight:400;color:var(--blue);font-size:20px;margin-top:22px}
.product .sub{font-size:11px;color:var(--muted);margin-bottom:16px}
.more{text-align:center;margin-top:26px}
.more .btn{background:var(--blue);padding:9px 30px}

/* recent posts */
.posts{height:520px;background:var(--white);padding-top:64px;border-top:1px solid var(--line)}
.posts-head{display:flex;justify-content:space-between;align-items:center}
.posts-head .section-title{color:#555;text-align:left}
.post-arrows{display:flex;gap:6px;color:var(--orange);font-size:16px;font-weight:700}
.post-grid{display:flex;gap:30px;margin-top:50px}
.post{width:300px}
.post-img{height:160px}
.post .date{display:inline-block;background:var(--blue);color:var(--white);font-size:10px;font-weight:700;padding:4px 12px;margin:14px 0 10px}
.post h5{font-size:13px;font-weight:600;color:#555;line-height:1.4;margin-bottom:8px}
.post p{font-size:11px;color:var(--muted);line-height:1.6}
.post p span{color:var(--orange)}

/* footer */
.footer{height:320px;background:var(--orange);color:var(--white);padding-top:56px}
.footer-cols{display:flex;justify-content:space-between}
.footer-col h6{font-size:13px;font-weight:700;margin-bottom:14px}
.footer-col li{list-style:none;font-size:11px;line-height:1.9;color:#fff3ea}
.socials{display:flex;gap:8px}
.socials span{width:16px;height:16px;border-radius:50%;background:rgba(255,255,255,.85)}
.copyright{height:24px;background:var(--orange-dark);color:#fff3ea;font-size:10px;text-align:center;line-height:24px}
</style>
</head>
<body>

<div class="topbar">
  <div class="container">
    <div class="search">
      <svg width="11" height="11" viewBox="0 0 12 12"><circle cx="5" cy="5" r="3.8" fill="none" stroke="#8a8a8a" stroke-width="1.5"/><line x1="8" y1="8" x2="11" y2="11" stroke="#8a8a8a" stroke-width="1.5"/></svg>
      Search here
    </div>
    <div class="top-links">
      <span class="btn">Sign up / Log in</span>
      <span>My Account</span>
      <span>Customer Care</span>
    </div>
  </div>
</div>

<header class="header">
  <div class="container">
    <div class="logo">
      <span class="logo-dot"></span>
      <div>
        <div class="logo-name">VitaBraid</div>
        <div class="logo-tag">Health management made simple</div>
      </div>
    </div>
    <nav class="nav">
      <div class="nav-item active">
        <svg width="26" height="24" viewBox="0 0 26 24"><path d="M3 12L13 3l10 9" fill="none" stroke="#8a8a8a" stroke-width="2"/><path d="M6 11v10h14V11" fill="none" stroke="#8a8a8a" stroke-width="2"/></svg>
        Home
      </div>
      <div class="nav-item">
        <svg width="26" height="24" viewBox="0 0 26 24"><rect x="3" y="4" width="20" height="16" rx="2" fill="none" stroke="#8a8a8a" stroke-width="2"/><path d="M7 15l4-4 3 3 5-5" fill="none" stroke="#8a8a8a" stroke-width="2"/></svg>
        Discount Dash
      </div>
      <div class="nav-item">
        <svg width="26" height="24" viewBox="0 0 26 24"><path d="M2 4h4l3 11h11l3-8H8" fill="none" stroke="#8a8a8a" stroke-width="2"/><circle cx="10" cy="20" r="1.8" fill="#8a8a8a"/><circle cx="19" cy="20" r="1.8" fill="#8a8a8a"/></svg>
        Shop
      </div>
      <div class="nav-item">
        <svg width="26" height="24" viewBox="0 0 26 24"><circle cx="13" cy="8" r="4" fill="none" stroke="#8a8a8a" stroke-width="2"/><path d="M5 22c0-5 4-8 8-8s8 3 8 8" fill="none" stroke="#8a8a8a" stroke-width="2"/></svg>
        Care Giver
      </div>
      <div class="nav-item">
        <svg width="26" height="24" viewBox="0 0 26 24"><circle cx="8" cy="8" r="3" fill="none" stroke="#8a8a8a" stroke-width="2"/><circle cx="18" cy="8" r="3" fill="none" stroke="#8a8a8a" stroke-width="2"/><path d="M2 20c0-4 3-6 6-6s6 2 6 6M12 20c0-4 3-6 6-6s6 2 6 6" fill="none" stroke="#8a8a8a" stroke-width="2"/></svg>
        Community
      </div>
    </nav>
  </div>
</header>

<section class="hero">
  <div class="hero-copy">
    <div class="kicker">We are Cloud based Health</div>
    <h1>Care Management system</h1>
    <span class="btn">Learn More</span>
  </div>
  <div class="hero-photo" role="img" aria-label="Photo of a smiling doctor with a stethoscope holding a tablet"></div>
  <div class="dots"><span></span><span></span><span></span><span></span><span></span></div>
</section>

<section class="features">
  <div class="container feature-row">
    <div class="feature">
      <svg width="34" height="24" viewBox="0 0 34 24"><path d="M2 12C8 3 26 3 32 12C26 21 8 21 2 12Z" fill="none" stroke="#fff" stroke-width="2.5"/><circle cx="17" cy="12" r="5" fill="#fff"/></svg>
      <h3>Overview</h3>
      <p>Track your vitals, appointments and daily activity in one secure cloud account that you can open from any device, at home or on the go.</p>
      <span class="btn">Learn More</span>
    </div>
    <div class="feature">
      <svg width="28" height="28" viewBox="0 0 28 28"><circle cx="14" cy="14" r="5" fill="none" stroke="#fff" stroke-width="3"/><path d="M14 2v5M14 21v5M2 14h5M21 14h5M5.5 5.5l3.5 3.5M19 19l3.5 3.5M5.5 22.5L9 19M19 9l3.5-3.5" stroke="#fff" stroke-width="3"/></svg>
      <h3>How it works</h3>
      <p>Connect your devices, invite your care team and let the dashboard gather your readings so trends and alerts appear automatically for you.</p>
      <span class="btn">Learn More</span>
    </div>
    <div class="feature">
      <svg width="30" height="28" viewBox="0 0 30 28"><path d="M2 9L15 2l13 7z" fill="#fff"/><rect x="5" y="11" width="3" height="11" fill="#fff"/><rect x="11" y="11" width="3" height="11" fill="#fff"/><rect x="17" y="11" width="3" height="11" fill="#fff"/><rect x="23" y="11" width="3" height="11" fill="#fff"/><rect x="2" y="24" width="26" height="3" fill="#fff"/></svg>
      <h3>Stores</h3>
      <p>Shop monitors, scales and wellness kits picked by our care experts, with member pricing and fast delivery straight to your front door.</p>
      <span class="btn">Learn More</span>
    </div>
    <div class="feature">
      <svg width="28" height="28" viewBox="0 0 28 28"><rect x="4" y="3" width="20" height="23" rx="2" fill="none" stroke="#fff" stroke-width="2.5"/><path d="M9 10h10M9 15h10M9 20h6" stroke="#fff" stroke-width="2.5"/></svg>
      <h3>Get Started</h3>
      <p>Create your free profile in minutes, choose a plan for yourself or your small business and begin managing health the smart way today.</p>
      <span class="btn">Learn More</span>
    </div>
  </div>
</section>

<section class="story">
  <div class="container">
    <h2 class="section-title title-lines">Our Success Story</h2>
    <span class="arrow" style="left:-20px">‹</span>
    <span class="arrow" style="right:-20px">›</span>
    <div class="story-body">
      <div class="avatar"><div role="img" aria-label="Portrait of a member"></div></div>
      <div class="story-text">
        <p>Since I started using the dashboard, my blood pressure and glucose readings are finally in one place. My doctor sees the same numbers I do, reminders keep me on schedule, and I have lost twelve pounds this year. Managing my health used to feel like a second job; now it takes a few minutes each morning and my whole family can follow my progress and cheer me on along the way.</p>
        <div class="story-name">Karen Holt</div>
        <div class="story-role">Member – Health care plan</div>
      </div>
    </div>
  </div>
</section>

<section class="videos">
  <h2 class="section-title">Featured Videos</h2>
  <div class="video-frame" role="img" aria-label="Video still of a nurse touching a digital health interface">
    <svg class="play" width="96" height="96" viewBox="0 0 96 96"><circle cx="48" cy="48" r="44" fill="#8dc63f" stroke="#fff" stroke-width="6"/><path d="M38 30l28 18-28 18z" fill="#fff"/></svg>
  </div>
</section>

<section class="products">
  <div class="container">
    <h2 class="section-title">Our Featured Products</h2>
    <div class="product-grid">
      <div class="product"><div class="product-img" role="img" aria-label="Wireless pulse sensor"></div><h4>Wireless Smart</h4><div class="sub">Glucose Monitoring System</div><svg width="26" height="26" viewBox="0 0 26 26"><circle cx="13" cy="13" r="12" fill="#8dc63f"/><path d="M13 7v12M7 13h12" stroke="#fff" stroke-width="2.5"/></svg></div>
      <div class="product"><div class="product-img" role="img" aria-label="Wireless blood pressure cuff"></div><h4>Wireless Smart</h4><div class="sub">Glucose Monitoring System</div><svg width="26" height="26" viewBox="0 0 26 26"><circle cx="13" cy="13" r="12" fill="#8dc63f"/><path d="M13 7v12M7 13h12" stroke="#fff" stroke-width="2.5"/></svg></div>
      <div class="product"><div class="product-img" role="img" aria-label="Smart body scale"></div><h4>Wireless Smart</h4><div class="sub">Glucose Monitoring System</div><svg width="26" height="26" viewBox="0 0 26 26"><circle cx="13" cy="13" r="12" fill="#8dc63f"/><path d="M13 7v12M7 13h12" stroke="#fff" stroke-width="2.5"/></svg></div>
      <div class="product"><div class="product-img" role="img" aria-label="Activity tracking wristband"></div><h4>Wireless Smart</h4><div class="sub">Glucose Monitoring System</div><svg width="26" height="26" viewBox="0 0 26 26"><circle cx="13" cy="13" r="12" fill="#8dc63f"/><path d="M13 7v12M7 13h12" stroke="#fff" stroke-width="2.5"/></svg></div>
      <div class="product"><div class="product-img" role="img" aria-label="Fingertip pulse oximeter"></div><h4>Wireless Smart</h4><div class="sub">Glucose Monitoring System</div><svg width="26" height="26" viewBox="0 0 26 26"><circle cx="13" cy="13" r="12" fill="#8dc63f"/><path d="M13 7v12M7 13h12" stroke="#fff" stroke-width="2.5"/></svg></div>
      <div class="product"><div class="product-img" role="img" aria-label="Clip-on activity tracker"></div><h4>Wireless Smart</h4><div class="sub">Glucose Monitoring System</div><svg width="26" height="26" viewBox="0 0 26 26"><circle cx="13" cy="13" r="12" fill="#8dc63f"/><path d="M13 7v12M7 13h12" stroke="#fff" stroke-width="2.5"/></svg></div>
    </div>
    <div class="more"><span class="btn">View More Products</span></div>
  </div>
</section>

<section class="posts">
  <div class="container">
    <div class="posts-head">
      <h2 class="section-title">Recent Posts</h2>
      <div class="post-arrows"><span>‹</span><span>›</span></div>
    </div>
    <div class="post-grid">
      <article class="post">
        <div class="post-img" role="img" aria-label="Hand touching a screen of medical icons" style="background:linear-gradient(135deg,#cfe6f3,#3f8fc0)"></div>
        <span class="date">JUN 12, 2015</span>
        <h5>Simple steps to keep your daily health records organised.</h5>
        <p>Small daily habits make a big difference. Learn how to log readings, set reminders and share results with your doctor in under five minutes a day. <span>Read More »</span></p>
      </article>
      <article class="post">
        <div class="post-img" role="img" aria-label="Medical team walking in a hospital corridor" style="background:linear-gradient(135deg,#e4ecf1,#6f9bb8)"></div>
        <span class="date">JUN 08, 2015</span>
        <h5>How care teams use the cloud to stay on the same page.</h5>
        <p>Doctors, nurses and family members can now view one shared timeline, so nothing is missed between visits and every update arrives right on time. <span>Read More »</span></p>
      </article>
      <article class="post">
        <div class="post-img" role="img" aria-label="Caregiver with an older couple at home" style="background:linear-gradient(135deg,#f1e6dc,#b4937a)"></div>
        <span class="date">JUN 02, 2015</span>
        <h5>Supporting older parents with smart home monitoring tools.</h5>
        <p>Gentle alerts and simple devices help seniors stay independent while giving loved ones peace of mind wherever they happen to live today. <span>Read More »</span></p>
      </article>
    </div>
  </div>
</section>

<footer class="footer">
  <div class="container footer-cols">
    <div class="footer-col"><h6>Company</h6><ul><li>About Us</li><li>Our Team</li><li>Careers</li><li>Partners</li><li>Press Room</li></ul></div>
    <div class="footer-col"><h6>Products</h6><ul><li>Blood Pressure Monitors</li><li>Activity Trackers</li><li>Smart Scales</li><li>Glucose Kits</li><li>Oximeters</li></ul></div>
    <div class="footer-col"><h6>Downloads</h6><ul><li>Mobile Apps</li><li>User Guides</li><li>Brochures</li><li>Desktop Sync</li></ul></div>
    <div class="footer-col"><h6>Contacts</h6><ul><li>Support</li><li>Shipping Info</li><li>Returns</li><li>Contact Us</li><li>Help Center</li></ul></div>
    <div class="footer-col"><h6>Follow Us</h6><div class="socials"><span></span><span></span><span></span><span></span><span></span><span></span><span></span></div></div>
  </div>
</footer>
<div class="copyright">© 2015 VitaBraid. All Rights Reserved.</div>

</body>
</html>
```